Velk Partners Building Business Cards

We need a business card that reflects our business as "Solar Experts" in San Diego. Browse our website www.velkpartners.example our License needs to be displayed as "CSLB# 3867140" our phone number is (619) 555-0187

Save thousands on your electric bills and increase the value of your home while helping to protect the environment. Our solar installation experts will help you design the system that's right for you, using only the highest quality equipment that will look great and give you ideal performance. Our goal is to make you energy independent, and get your electric bill to 0.

Paul Osterby
(619) 555-0187
paul@velkpartners.example

Target Market(s)

Home owners in san diego looking for solar

Industry/Entity Type

Solar Energy

Contact Information for Business Card

Paul Osterby
(619) 555-0187
paul@velkpartners.example

Font styles to use
Other font styles liked:
• Use our logo font

Requirements
Must have
• License needs to be displayed as "CSLB# 3867140" our phone number is (619) 555-0187
Nice to have
• Real images of rooftop home solar in san diego
Should not have
• our business address

```html
<!DOCTYPE html>
<html lang="en">
<head>
<meta charset="utf-8">
<title>Velk Partners Building — Business Cards</title>
<link rel="stylesheet" href="https://fonts.googleapis.com/css2?family=PT+Sans:ital,wght@0,400;0,700;1,400&display=swap">
<style>
  :root {
    --navy: #1b3c73;
    --sun: #f6ad12;
    --ink-grey: #555a60;
    --paper: #ffffff;
    --backdrop: #474747;
    --rule: #c9ccd1;
  }
  * { margin: 0; padding: 0; box-sizing: border-box; }
  html, body {
    width: 1105px; height: 1200px; overflow: hidden;
    background: var(--backdrop);
    font-family: "PT Sans", sans-serif;
  }
  .card {
    position: absolute; left: 193px; width: 720px; height: 410px;
    box-shadow: 0 4px 12px rgba(0,0,0,.35);
  }
  .card--front { top: 167px; background: var(--paper); }
  .card--back { top: 623px; background: var(--navy); }

  .wordmark {
    position: absolute; font-weight: 700; font-size: 36px; line-height: 1.05;
    text-align: center; letter-spacing: -0.3px;
  }
  .card--front .wordmark { left: 40px; top: 132px; width: 320px; color: var(--navy); }
  .card--back .wordmark { left: 0; top: 168px; width: 720px; color: var(--paper); font-size: 44px; }

  .divider {
    position: absolute; left: 384px; top: 93px; width: 1px; height: 174px;
    background: var(--rule);
  }
  .contact { position: absolute; left: 418px; top: 90px; }
  .contact__name { font-size: 25px; font-weight: 700; color: var(--navy); line-height: 1; }
  .contact__title { font-size: 19px; color: var(--sun); margin-top: 6px; line-height: 1; }
  .contact__license { font-size: 17px; color: var(--ink-grey); margin-top: 20px; line-height: 1; }
  .contact__line {
    display: flex; align-items: center; gap: 10px;
    font-size: 17px; color: var(--ink-grey); line-height: 1;
  }
  .contact__line--phone { margin-top: 22px; }
  .contact__line--email { margin-top: 9px; }
  .contact__icon { width: 16px; height: 16px; fill: var(--navy); flex: none; }

  .band { position: absolute; left: 0; top: 356px; width: 720px; height: 36px; display: flex; }
  .band__main { flex: 0 0 605px; background: var(--navy); display: flex; align-items: center; padding-left: 122px; }
  .band__accent { flex: 1; background: var(--sun); }
  .band__url { color: var(--paper); font-size: 18px; letter-spacing: 3px; }

  .back-url {
    position: absolute; left: 0; top: 338px; width: 720px; text-align: center;
    color: var(--paper); font-style: italic; font-size: 19px; letter-spacing: 6px;
  }
</style>
</head>
<body>
  <section class="card card--front" aria-label="Business card front">
    <div class="wordmark">Velk Partners<br>Building</div>
    <div class="divider"></div>
    <div class="contact">
      <p class="contact__name">Paul Osterby</p>
      <p class="contact__title">CEO/Founder</p>
      <p class="contact__license">CSLB# 3867140</p>
      <p class="contact__line contact__line--phone">
        <svg class="contact__icon" viewBox="0 0 24 24" aria-hidden="true"><path d="M6.6 10.8c1.4 2.8 3.8 5.1 6.6 6.6l2.2-2.2c.3-.3.7-.4 1-.2 1.1.4 2.3.6 3.6.6.6 0 1 .4 1 1V20c0 .6-.4 1-1 1C10.6 21 3 13.4 3 4c0-.6.4-1 1-1h3.5c.6 0 1 .4 1 1 0 1.3.2 2.5.6 3.6.1.3 0 .7-.2 1z"/></svg>
        (619) 555-0187
      </p>
      <p class="contact__line contact__line--email">
        <svg class="contact__icon" viewBox="0 0 24 24" aria-hidden="true"><path d="M2 5h20v14H2z M4 7v.4l8 5 8-5V7z" fill-rule="evenodd"/></svg>
        paul@velkpartners.example
      </p>
    </div>
    <div class="band">
      <div class="band__main"><span class="band__url">www.velkpartners.example</span></div>
      <div class="band__accent"></div>
    </div>
  </section>

  <section class="card card--back" aria-label="Business card back">
    <div class="wordmark">Velk Partners Building</div>
    <p class="back-url">www.velkpartners.example</p>
  </section>
</body>
</html>
```